Veltrano.co - Polar Expeditions Specialists

We need a modern, visually striking business card for Veltrano.co, a company specialized in selling expedition cruises to the most remote regions on Earth, with a focus on the Arctic and Antarctica. The design should instantly communicate that the cardholder is an expert in polar travel. Use clean, premium aesthetics with cool tones like icy blue and white, possibly incorporating polar imagery (ice, glaciers, penguins, etc.)

Attached the logo

Contact Information for Business Card

Feels high-end and trustworthy.. Visually memorable — encourages people to keep it

Colors
0054AA
0677BA
7BADD7
CADEEF
E8F1F8

Requirements
Must have
• ice, glaciers, penguins, montains
Nice to have
• modern, transparente,

```html
<!DOCTYPE html>
<html lang="en">
<head>
<meta charset="utf-8">
<title>Veltrano.co Business Card</title>
<link href="https://fonts.googleapis.com/css2?family=Poppins:wght@400;500;600;700&family=Montserrat:wght@400;500&display=swap" rel="stylesheet">
<style>
  :root {
    --page-bg: #2b2b2d;
    --brand-blue: #2f6db5;
    --back-blue: #3575b8;
    --back-ink: #2a62a6;
    --back-ink-light: #5a92cc;
    --deep-blue: #0054aa;
    --ink: #1c1c1c;
    --white: #ffffff;
    --rule: #7badd7;
  }
  * { box-sizing: border-box; margin: 0; padding: 0; }
  html, body { width: 1200px; height: 875px; overflow: hidden; }
  body {
    background: var(--page-bg);
    font-family: "Poppins", sans-serif;
    display: flex;
    align-items: center;
    justify-content: center;
    gap: 40px;
  }
  .card {
    width: 540px;
    height: 309px;
    border-radius: 18px;
    position: relative;
    overflow: hidden;
    box-shadow: 0 18px 40px rgba(0,0,0,.45);
  }

  /* Back side */
  .card-back {
    background: var(--back-blue);
    display: flex;
    align-items: center;
    justify-content: center;
  }
  .back-logo { display: flex; align-items: center; gap: 16px; }
  .back-logo .mark {
    width: 58px; height: 58px; border-radius: 50%;
    background: var(--back-ink);
  }
  .back-logo .name {
    font-weight: 700; font-size: 54px; line-height: 1;
    color: var(--back-ink); letter-spacing: .5px;
  }
  .back-logo .tagline {
    font-weight: 600; font-size: 15px; color: var(--back-ink-light);
    margin-top: 6px; letter-spacing: .3px;
  }

  /* Front side */
  .card-front { background: var(--white); }
  .polar-art {
    position: absolute; right: 0; top: 0;
    width: 215px; height: 100%;
    background: radial-gradient(ellipse at 60% 45%, #3a78bf 0%, #4a86c8 45%, rgba(123,173,215,.35) 75%, rgba(255,255,255,0) 100%);
  }
  .front-content { position: absolute; left: 34px; top: 58px; }
  .brand-name {
    font-weight: 700; font-size: 58px; line-height: 1;
    color: var(--brand-blue); letter-spacing: .5px;
  }
  .brand-tagline {
    font-weight: 600; font-size: 15px; color: var(--brand-blue);
    margin: 4px 0 0 30px; letter-spacing: .2px;
  }
  .details { display: flex; align-items: stretch; margin: 14px 0 0 50px; }
  .person { padding-right: 12px; border-right: 1px solid var(--rule); padding-top: 14px; }
  .person-name { font-weight: 700; font-size: 20px; color: var(--brand-blue); line-height: 1.1; }
  .person-title { font-family: "Montserrat", sans-serif; font-size: 12px; color: var(--ink); text-align: right; }
  .contacts { list-style: none; padding-left: 12px; font-family: "Montserrat", sans-serif; font-size: 12px; color: var(--ink); }
  .contacts li { display: flex; align-items: center; gap: 6px; line-height: 1.55; }
  .contacts svg { width: 11px; height: 11px; fill: var(--brand-blue); flex: none; }
  .address {
    font-family: "Montserrat", sans-serif; font-size: 12px; color: var(--ink);
    margin: 18px 0 0 60px;
  }
</style>
</head>
<body>
  <section class="card card-back">
    <div class="back-logo">
      <span class="mark"></span>
      <div>
        <div class="name">Veltrano.co</div>
        <div class="tagline">Polar Expeditions Specialists</div>
      </div>
    </div>
  </section>

  <section class="card card-front">
    <div class="polar-art" role="img" aria-label="Blue silhouette illustration of a polar bear"></div>
    <div class="front-content">
      <div class="brand-name">Veltrano.co</div>
      <div class="brand-tagline">Polar Expeditions Specialists</div>
      <div class="details">
        <div class="person">
          <div class="person-name">Marco Ellison</div>
          <div class="person-title">Managing Director</div>
        </div>
        <ul class="contacts">
          <li><svg viewBox="0 0 24 24"><path d="M6.6 10.8a15.1 15.1 0 0 0 6.6 6.6l2.2-2.2a1 1 0 0 1 1-.25 11.4 11.4 0 0 0 3.6.57 1 1 0 0 1 1 1V20a1 1 0 0 1-1 1A17 17 0 0 1 3 4a1 1 0 0 1 1-1h3.5a1 1 0 0 1 1 1c0 1.25.2 2.45.57 3.57a1 1 0 0 1-.25 1z"/></svg>(555)214-7730</li>
          <li><svg viewBox="0 0 24 24"><path d="M2 5h20v14H2zm2 2v.5l8 5 8-5V7l-8 5z"/></svg>info@veltrano.co</li>
          <li><svg viewBox="0 0 24 24"><path d="M12 2a10 10 0 1 0 0 20 10 10 0 0 0 0-20zm0 2c.9 1.2 1.6 2.6 2 4h-4c.4-1.4 1.1-2.8 2-4zM4.3 14a8 8 0 0 1 0-4h3.4a16 16 0 0 0 0 4zm5.7 0a14 14 0 0 1 0-4h4a14 14 0 0 1 0 4zm6.3 0a16 16 0 0 0 0-4h3.4a8 8 0 0 1 0 4zM12 20c-.9-1.2-1.6-2.6-2-4h4c-.4 1.4-1.1 2.8-2 4z"/></svg>www.veltrano.co</li>
        </ul>
      </div>
      <div class="address">42 Harbor View Lane Eastbrook, NJ 07011 USA</div>
    </div>
  </section>
</body>
</html>
```